Stationary Set Rebrand for Brennick

We are a Canadian Distribution and Service Company that was established in 1969. Over the past 5 decades we have expanded our business and have warehouses across Canada. We specialize in adhesive tapes, adhesives, films, safety, warehouse, shipping, janitorial and packaging supplies.

We have updated our logo design and would like a new corporate branding identity that includes a new fresh Stationary Set (Business Cards, Letterhead, Letterhead MS Word, Envelope, Presentation Folders, Email Signatures, Notepad Covers, etc.)

Target Market(s)

Industrial Business Sector

Font styles to use
Sans Serif

Colors
0054AA
0677BA
7BADD7
CADEEF
E8F1F8
0094D4
00A9DD
6FCCEA
C7EBF8
E9F6FB
00AB8E
00BBA5
67D7C9
C6EFE9
E9F9F6
EB3D1F
EC4F4E
F09395
F8D3D4
FCEDEE

Requirements
Should not have
• Colors not too light, darker colours preferred

```html
<!DOCTYPE html>
<html lang="en">
<head>
<meta charset="utf-8">
<title>Brennick Stationery Set</title>
<link href="https://fonts.googleapis.com/css2?family=Montserrat:wght@400;500;700;800&family=Open+Sans:wght@400;600;700&display=swap" rel="stylesheet">
<style>
:root{
  --bg:#dde2e5;
  --ink:#1c1b23;
  --red:#e01b26;
  --paper:#ffffff;
  --rule:#3a3a3a;
  --muted:#8c8c92;
  --line:#c9c9cf;
}
*{box-sizing:border-box;margin:0;padding:0}
html,body{width:1200px;height:711px;overflow:hidden;background:var(--bg)}
body{position:relative;font-family:"Montserrat",sans-serif;color:var(--ink)}
.piece{position:absolute;overflow:hidden;box-shadow:0 4px 10px rgba(0,0,0,.22)}
.piece>svg.wave{position:absolute;inset:0;width:100%;height:100%}
.abs{position:absolute}
.brand{font-family:"Montserrat",sans-serif;font-weight:800;letter-spacing:-.02em;line-height:1}
.brand-light{color:var(--paper)}
.brand-dark{color:var(--ink)}
.tagline{font-family:"Montserrat",sans-serif;font-weight:500;line-height:1}
.contact{font-family:"Montserrat",sans-serif;color:var(--paper);text-align:right;line-height:1.45}
.contact .ico{display:inline-block;border:1px solid var(--paper);border-radius:50%;vertical-align:middle}
.person-name{font-family:"Montserrat",sans-serif;color:var(--red);font-weight:500;line-height:1}
.person-name b{font-weight:700}
.person-role{font-family:"Montserrat",sans-serif;color:var(--paper);font-weight:500}

/* envelope */
.envelope-front{left:51px;top:55px;width:282px;height:126px;background:var(--ink)}
.envelope-back{left:52px;top:193px;width:281px;height:125px;background:var(--ink)}
.envelope-flap{left:4px;top:0;width:273px;height:42px;border-radius:0 0 10px 10px;background:#222129;box-shadow:0 3px 6px rgba(0,0,0,.35)}
.seal-dot{left:134px;top:16px;width:13px;height:13px;border-radius:50%;background:var(--red)}

/* business cards */
.card-back{left:53px;top:329px;width:274px;height:156px;border-radius:9px;background:var(--ink);border-bottom:2px solid var(--red)}
.card-pattern{inset:0;background:linear-gradient(160deg,#2b2a33 0%,#1c1b23 55%,#141319 100%)}
.card-front{left:53px;top:501px;width:275px;height:156px;border-radius:9px;background:var(--ink)}

/* letterhead */
.letterhead{left:367px;top:57px;width:330px;height:466px;background:var(--paper)}
.letter-body{font-family:"Open Sans",sans-serif;font-size:6.6px;line-height:1.3;color:#222;text-align:justify}
.letter-body p{margin-bottom:6.5px}
.addressee{font-family:"Open Sans",sans-serif;font-size:6.2px;line-height:1.3;color:#222}
.addressee strong{font-size:8.4px;font-weight:700;display:block;line-height:1.1}
.signature-mark{background:linear-gradient(90deg,rgba(28,27,35,.18),rgba(28,27,35,.06));border-radius:3px}
.signer-name{font-family:"Open Sans",sans-serif;font-weight:700;font-size:14px;line-height:1}
.signer-role{font-family:"Open Sans",sans-serif;font-size:6.2px}

/* email signature */
.email-signature{left:365px;top:546px;width:331px;height:110px;background:var(--ink)}
.social-dot{width:5px;height:5px;border-radius:50%;background:var(--paper)}

/* folders */
.folder-insert{left:840px;top:68px;width:40px;height:190px;background:var(--paper);box-shadow:0 3px 8px rgba(0,0,0,.2)}
.folder-cover{left:727px;top:45px;width:122px;height:237px;background:var(--ink)}
.folder-open{left:912px;top:60px;width:228px;height:211px;background:#f3f3f4}
.folder-spine{left:113px;top:0;width:2px;height:100%;background:#d2d2d6}
.folder-sheet{left:118px;top:8px;width:104px;height:150px;background:var(--paper);box-shadow:0 1px 4px rgba(0,0,0,.15)}
.sheet-text{font-family:"Open Sans",sans-serif;font-size:3.2px;line-height:1.35;color:#333}

/* notebook */
.notebook-cover{left:820px;top:290px;width:240px;height:160px;border-radius:4px;background:var(--ink)}
.cover-pattern{inset:0;background:linear-gradient(135deg,#34333c 0%,#1f1e26 60%,#16151b 100%)}
.cover-coil{left:-4px;top:6px;width:8px;height:148px;background:repeating-linear-gradient(180deg,#b9b9bf 0 2px,transparent 2px 5px)}
.notebook-pages{left:782px;top:462px;width:273px;height:192px;background:var(--paper)}
.page{top:0;width:136px;height:192px}
.page-left{left:0}
.page-right{left:137px}
.notes-label{font-family:"Open Sans",sans-serif;font-size:5px;color:var(--red);font-weight:600}
.date-label{font-family:"Open Sans",sans-serif;font-size:3.6px;color:var(--muted);font-style:italic}
.ruled{left:10px;right:8px;top:38px;height:145px;background:repeating-linear-gradient(180deg,transparent 0 9px,var(--line) 9px 10px)}
.page-brand{right:8px;top:10px;text-align:right;border-bottom:1.5px solid var(--red);padding-bottom:2px}
.spiral{left:131px;top:2px;width:10px;height:188px;background:repeating-linear-gradient(180deg,#8a8a90 0 2px,transparent 2px 5px)}
</style>
</head>
<body>

<!-- Envelope front -->
<section class="piece envelope-front">
  <svg class="wave" viewBox="0 0 282 126" preserveAspectRatio="none" aria-hidden="true">
    <path d="M0 88 C70 128 160 118 210 78 C238 60 262 58 282 62 L282 126 L0 126Z" fill="var(--red)"/>
    <path d="M0 88 C30 108 70 118 110 118 C70 114 30 102 0 94Z" fill="var(--paper)"/>
  </svg>
  <div class="abs" style="left:20px;top:11px">
    <div class="brand brand-light" style="font-size:21px">Brennick</div>
    <div class="tagline" style="font-size:4.6px;color:var(--paper);margin-top:2px">Tape and Packaging Specialists</div>
  </div>
  <div class="abs" style="left:232px;top:38px;width:20px;height:20px;border-radius:50%;background:var(--red)"></div>
  <div class="abs contact" style="right:13px;top:77px;font-size:5.8px">
    (416) 555-0147 <span class="ico" style="width:4px;height:4px"></span><br>
    info@brennicksupply.ca <span class="ico" style="width:4px;height:4px"></span><br>
    www.brennicksupply.ca <span class="ico" style="width:4px;height:4px"></span><br>
    480 Harbourline Rd. Suite 12 <span class="ico" style="width:4px;height:4px"></span><br>
    Hamilton, ON L8N 2B4 &nbsp;&nbsp;
  </div>
</section>

<!-- Envelope back -->
<section class="piece envelope-back">
  <div class="abs envelope-flap"></div>
  <div class="abs seal-dot"></div>
</section>

<!-- Business card back -->
<section class="piece card-back">
  <div class="abs card-pattern" role="img" aria-label="Tonal pattern of small emblems across dark background"></div>
  <div class="abs" style="left:54px;top:54px">
    <div class="brand brand-light" style="font-size:38px">Brennick</div>
    <div class="tagline" style="font-size:8.4px;color:var(--paper);margin-top:3px">Tape and Packaging Specialists</div>
  </div>
</section>

<!-- Business card front -->
<section class="piece card-front">
  <svg class="wave" viewBox="0 0 275 156" preserveAspectRatio="none" aria-hidden="true">
    <path d="M0 124 C70 166 170 150 215 112 C240 96 258 96 275 98 L275 156 L0 156Z" fill="var(--red)"/>
    <path d="M0 124 C35 142 75 150 120 150 C75 146 35 134 0 130Z" fill="var(--paper)"/>
  </svg>
  <div class="abs" style="left:8px;top:11px">
    <div class="brand brand-light" style="font-size:27px">Brennick</div>
    <div class="tagline" style="font-size:6.3px;color:var(--paper);margin-top:3px">Tape and Packaging Specialists</div>
  </div>
  <div class="abs" style="right:11px;top:13px;text-align:right">
    <div class="person-name" style="font-size:14px"><b>Mira</b> Solberg</div>
    <div class="person-role" style="font-size:7px;margin-top:2px">Founder &amp; CEO</div>
  </div>
  <div class="abs" style="left:220px;top:70px;width:26px;height:26px;border-radius:50%;background:var(--red)"></div>
  <div class="abs contact" style="left:12px;top:92px;text-align:left;font-size:7.6px;line-height:1.4">
    <span class="ico" style="width:4px;height:4px;border-color:var(--red)"></span> (416) 555-0147<br>
    <span class="ico" style="width:4px;height:4px;border-color:var(--red)"></span> info@brennicksupply.ca<br>
    <span class="ico" style="width:4px;height:4px;border-color:var(--red)"></span> www.brennicksupply.ca
  </div>
  <div class="abs contact" style="right:12px;top:132px;font-size:7.6px;line-height:1.3">
    480 Harbourline Rd. Suite 12<br>Hamilton, ON L8N 2B4
  </div>
</section>

<!-- Letterhead -->
<section class="piece letterhead">
  <svg class="wave" viewBox="0 0 330 466" preserveAspectRatio="none" aria-hidden="true">
    <line x1="17" y1="52.5" x2="312" y2="52.5" stroke="var(--rule)" stroke-width="0.8"/>
    <line x1="111" y1="52.5" x2="218" y2="52.5" stroke="var(--red)" stroke-width="2"/>
    <path d="M0 412 C60 470 150 450 220 405 C262 380 300 382 330 392 L330 466 L0 466Z" fill="var(--red)"/>
    <path d="M0 412 C40 440 90 452 140 450 C90 446 40 432 0 420Z" fill="var(--ink)"/>
  </svg>
  <div class="abs" style="left:0;right:0;top:17px;text-align:center">
    <div class="brand brand-dark" style="font-size:22px">Brennick</div>
    <div class="tagline" style="font-size:4.8px;margin-top:2px">Tape and Packaging Specialists</div>
  </div>
  <div class="abs addressee" style="left:18px;top:113px">August-05-2019</div>
  <div class="abs addressee" style="left:18px;top:127px">
    <strong>Dana Pryce</strong>Director<br><br>480 Harbourline Rd. Suite 12<br>Hamilton, ON L8N 2B4
  </div>
  <div class="abs addressee" style="left:18px;top:179px"><strong>Dana Pryce</strong></div>
  <div class="abs letter-body" style="left:18px;top:197px;width:294px">
    <p>Lorem ipsum dolor sit amet, consectetuer adipiscing elit, sed diam nonummy nibh euismod tincidunt ut laoreet dolore magna aliquam erat volutpat. Ut wisi enim ad minim veniam, quis nostrud exerci tation ullamcorper suscipit lobortis</p>
    <p>Lorem ipsum dolor sit amet, cons ectetuer adipiscing elit, sed diam nonummy nibh euismod tincidunt ut laoreet dolore magna aliquam erat volutpat. Ut wisi enim ad minim veniam, quis nostrud exerci tation ullamcorper suscipit lobortis nisl ut aliquip ex ea commodo consequat. Lorem ipsum dolor sit amet, consectetuer olutpat. Ut wisi enim ad minim veniam, quis nostrud exerci tation ullamcorper suscipit lobortis nisl ut aliquip ex ea commodo consequat. Duis autem</p>
    <p>vel eum iriure dolor in hendrerit in vulputate velit esse molestie consequat, vel illum dolore eu feugiat nulla facilisis at vero eros et accumsan et iusto odio dignissim qui blandit praesent luptatum zzril delenit augue duis dolore te feugait nulla facilisi. Lorem ipsum dolor sit amet, cons ectetuer adipiscing elit, sed diam nonummy nibh euismod tincidunt ut laoreet dolore magna aliquam erat volutpat. Ut wisi enim .</p>
  </div>
  <div class="abs signature-mark" role="img" aria-label="Handwritten signature" style="left:18px;top:346px;width:88px;height:20px"></div>
  <div class="abs" style="left:18px;top:369px">
    <div class="signer-name">Owen Hale</div>
    <div class="signer-role" style="margin-top:2px">Co-Founder</div>
  </div>
  <div class="abs" style="left:268px;top:358px;width:26px;height:26px;border-radius:50%;background:var(--red)"></div>
  <div class="abs contact" style="right:16px;top:418px;font-size:6.9px;line-height:1.3">
    (416) 555-0147 <span class="ico" style="width:4.5px;height:4.5px"></span><br>
    info@brennicksupply.ca <span class="ico" style="width:4.5px;height:4.5px"></span><br>
    www.brennicksupply.ca <span class="ico" style="width:4.5px;height:4.5px"></span><br>
    <span style="display:inline-block;margin-top:2px">480 Harbourline Rd. Suite 12 Hamilton, ON L8N 2B4</span> <span class="ico" style="width:4.5px;height:4.5px"></span>
  </div>
</section>

<!-- Email signature -->
<section class="piece email-signature">
  <svg class="wave" viewBox="0 0 331 110" preserveAspectRatio="none" aria-hidden="true">
    <path d="M0 74 C70 118 170 104 230 62 C262 46 300 46 331 52 L331 110 L0 110Z" fill="var(--red)"/>
    <path d="M0 74 C35 90 80 98 125 96 C80 94 35 84 0 80Z" fill="var(--paper)"/>
  </svg>
  <div class="abs" style="left:14px;top:18px">
    <div class="brand brand-light" style="font-size:26px">Brennick</div>
    <div class="tagline" style="font-size:6.3px;color:var(--paper);margin-top:3px">Tape and Packaging Specialists</div>
  </div>
  <div class="abs" style="right:16px;top:8px;text-align:right">
    <div class="person-name" style="font-size:13.5px"><b>Mira</b> Solberg</div>
    <div class="person-role" style="font-size:6.6px;margin-top:1px">Founder &amp; CEO</div>
  </div>
  <div class="abs" style="left:274px;top:35px;width:18px;height:18px;border-radius:50%;background:var(--red)"></div>
  <div class="abs contact" style="right:15px;top:69px;font-size:6.8px;line-height:1.3">
    (416) 555-0147 <span class="ico" style="width:4px;height:4px"></span><br>
    info@brennicksupply.ca <span class="ico" style="width:4px;height:4px"></span><br>
    www.brennicksupply.ca <span class="ico" style="width:4px;height:4px"></span><br>
    <span style="display:inline-block;margin-top:2px">480 Harbourline Rd. Suite 12 Hamilton, ON L8N 2B4</span> <span class="ico" style="width:4px;height:4px"></span>
  </div>
  <div class="abs" style="left:5px;top:102px;display:flex;gap:3.5px">
    <span class="social-dot"></span><span class="social-dot"></span><span class="social-dot"></span><span class="social-dot"></span><span class="social-dot"></span>
  </div>
</section>

<!-- Presentation folder, closed -->
<section class="piece folder-insert" aria-hidden="true">
  <svg class="wave" viewBox="0 0 40 190" preserveAspectRatio="none">
    <g stroke="#bbb" stroke-width="0.8">
      <line x1="2" y1="24" x2="36" y2="24"/><line x1="2" y1="84" x2="36" y2="84"/><line x1="2" y1="88" x2="36" y2="88"/>
      <line x1="2" y1="96" x2="36" y2="96"/><line x1="2" y1="100" x2="36" y2="100"/><line x1="2" y1="104" x2="36" y2="104"/>
      <line x1="2" y1="118" x2="36" y2="118"/><line x1="2" y1="122" x2="36" y2="122"/>
    </g>
    <rect x="0" y="130" width="40" height="60" fill="var(--red)"/>
  </svg>
</section>
<section class="piece folder-cover">
  <svg class="wave" viewBox="0 0 122 237" preserveAspectRatio="none" aria-hidden="true">
    <path d="M0 212 C35 240 80 222 95 205 C105 196 115 196 122 198 L122 237 L0 237Z" fill="var(--red)"/>
    <path d="M0 212 C14 224 34 230 52 230 C32 226 14 220 0 216Z" fill="var(--paper)"/>
  </svg>
  <div class="abs" style="right:9px;top:12px;text-align:right">
    <div class="brand brand-light" style="font-size:14px">Brennick</div>
    <div class="tagline" style="font-size:3.3px;color:var(--paper);margin-top:1px">Tape and Packaging Specialists</div>
  </div>
  <div class="abs" style="left:94px;top:183px;width:16px;height:16px;border-radius:50%;background:var(--red)"></div>
</section>

<!-- Presentation folder, open -->
<section class="piece folder-open">
  <div class="abs folder-spine"></div>
  <div class="abs folder-sheet">
    <div class="abs" style="right:8px;top:8px;text-align:right">
      <div class="brand brand-dark" style="font-size:9px">Brennick</div>
      <div class="tagline" style="font-size:2.4px">Tape and Packaging Specialists</div>
    </div>
    <div class="abs" style="left:6px;right:6px;top:25px;border-top:0.6px solid var(--rule)"></div>
    <div class="abs sheet-text" style="left:6px;top:50px;width:92px">
      <strong>Dana Pryce</strong><br>Director<br><br>
      Thank you for your order. Shipping details follow below.
    </div>
    <div class="abs" style="left:6px;right:6px;top:74px;height:56px;background:repeating-linear-gradient(180deg,#c8c8cc 0 0.7px,transparent 0.7px 4.5px)"></div>
  </div>
  <svg class="wave" viewBox="0 0 228 211" preserveAspectRatio="none" aria-hidden="true">
    <path d="M0 172 L0 211 L113 211 L113 180 C105 160 80 152 60 158 C40 164 20 170 0 172Z" fill="var(--red)"/>
    <path d="M0 160 L0 211 L113 211 L113 175 C100 155 80 152 60 154 C40 156 20 160 0 160Z" fill="var(--red)"/>
    <path d="M115 211 L228 211 L228 160 C190 150 150 150 130 165 C120 172 116 185 115 211Z" fill="var(--red)"/>
  </svg>
  <div class="abs" style="left:42px;top:170px;width:20px;height:20px;border-radius:50%;border:1.2px solid var(--paper)"></div>
  <div class="abs" style="left:168px;top:170px;width:20px;height:20px;border-radius:50%;border:1.2px solid var(--paper)"></div>
</section>

<!-- Notebook cover -->
<section class="piece notebook-cover">
  <div class="abs cover-pattern" role="img" aria-label="Tonal pattern of small emblems across dark cover"></div>
  <div class="abs cover-coil"></div>
  <div class="abs" style="left:86px;top:28px;width:70px;height:70px;border-radius:50%;background:var(--red)"></div>
  <div class="abs" style="right:14px;bottom:14px;text-align:right">
    <div class="brand brand-light" style="font-size:17px">Brennick</div>
    <div class="tagline" style="font-size:3.9px;color:var(--paper);margin-top:1px">Tape and Packaging Specialists</div>
  </div>
</section>

<!-- Notebook pages -->
<section class="piece notebook-pages">
  <div class="abs page page-left">
    <div class="abs notes-label" style="left:10px;top:14px">Notes</div>
    <div class="abs date-label" style="left:10px;top:21px">Date Of ____________</div>
    <div class="abs page-brand">
      <div class="brand brand-dark" style="font-size:10px">Brennick</div>
      <div class="tagline" style="font-size:2.4px">Tape and Packaging Specialists</div>
    </div>
    <div class="abs ruled"></div>
  </div>
  <div class="abs page page-right">
    <div class="abs notes-label" style="left:10px;top:14px">Notes</div>
    <div class="abs date-label" style="left:10px;top:21px">Date Of ____________</div>
    <div class="abs page-brand">
      <div class="brand brand-dark" style="font-size:10px">Brennick</div>
      <div class="tagline" style="font-size:2.4px">Tape and Packaging Specialists</div>
    </div>
    <div class="abs ruled"></div>
  </div>
  <div class="abs spiral"></div>
</section>

</body>
</html>
```